New Innovative Counselling and psychotherapy Service needs Business Card design

Keep it simple and professional. On one side, just company name and logo (perhaps in all blue) and maybe a tag line.

On other side (all white) my name and Qualifications in centre

Industry/Entity Type

Health And Wellness

Contact Information for Business Card

Dara Whelby
Counsellor & Psychotherapist
BSc (Psychol.), BA, Dip. (Couns. & Psych.), PG.Cert (CBT), FGTrK, ONRE

I will also require Mobile no, Email and web site address of which I'll pass on to final designer.

Font styles to use
Sans Serif

Requirements
Must have
• My Logo Only and please use the colours in logo that is in it.
Should not have
• Any other images

```html
<!DOCTYPE html>
<html lang="en">
<head>
<meta charset="utf-8">
<title>Thrive Lane – Business Card</title>
<link rel="stylesheet" href="https://fonts.googleapis.com/css2?family=Lato:wght@400;700&family=Oswald:wght@400&display=swap">
<style>
  :root {
    --backdrop: #e9e4dc;
    --card-light: #d3b088;
    --card-mid: #c49b6c;
    --card-dark: #b58a5b;
    --ink: #17110b;
    --rule: #5a4330;
  }
  * { margin: 0; padding: 0; box-sizing: border-box; }
  html, body { width: 1200px; height: 900px; overflow: hidden; }
  body {
    background: var(--backdrop);
    position: relative;
    font-family: "Lato", sans-serif;
    color: var(--ink);
  }
  .card {
    position: absolute;
    left: 330px;
    width: 556px;
    height: 343px;
    background: radial-gradient(ellipse at 40% 0%, var(--card-light) 0%, var(--card-mid) 55%, var(--card-dark) 100%);
    box-shadow: 3px 4px 8px rgba(0,0,0,0.35);
    text-align: center;
  }
  .card--contact { top: 90px; }
  .card--brand { top: 470px; }

  .holder-name {
    position: absolute; top: 164px; left: 0; right: 0;
    font-size: 20px; letter-spacing: 0.3px; font-weight: 400;
  }
  .card--contact .holder-name { top: 74px; }
  .holder-role {
    position: absolute; top: 102px; left: 0; right: 0;
    font-size: 15px; line-height: 20.5px;
  }
  .divider {
    position: absolute; top: 192px; left: 173px; width: 208px; height: 22px;
  }
  .contact-list {
    position: absolute; top: 221px; left: 0; right: 0;
    list-style: none; font-size: 15px; line-height: 20.5px;
  }

  .brand {
    position: absolute; top: 118px; left: 86px;
    display: flex; align-items: center; gap: 26px;
  }
  .brand-dot {
    width: 76px; height: 76px; border-radius: 50%; background: var(--ink);
  }
  .brand-name {
    font-size: 37px; font-weight: 400; letter-spacing: -0.3px;
  }
  .tagline {
    position: absolute; top: 254px; left: 0; right: 0;
    font-family: "Oswald", sans-serif; font-size: 17.5px; letter-spacing: 0.2px;
  }
</style>
</head>
<body>
  <section class="card card--contact">
    <h1 class="holder-name">DARA WHELBY</h1>
    <p class="holder-role">Counsellor &amp; Psychotherapist<br>BSc (Psychol.), BA, Dip. (Couns. &amp; Psych.),<br>PG.Cert (CBT), FGTrK, ONRE</p>
    <svg class="divider" viewBox="0 0 208 22" aria-hidden="true">
      <line x1="0" y1="11" x2="68" y2="11" stroke="var(--rule)" stroke-width="0.8"/>
      <line x1="140" y1="11" x2="208" y2="11" stroke="var(--rule)" stroke-width="0.8"/>
      <g fill="var(--ink)">
        <rect x="73" y="2" width="18" height="18" rx="2"/>
        <rect x="95" y="2" width="18" height="18" rx="2"/>
        <rect x="117" y="2" width="18" height="18" rx="2"/>
      </g>
      <g fill="none" stroke="var(--card-light)" stroke-width="1.3">
        <path d="M76.5 10 q5.5 -4 11 0 M78 10 v3 h8 v-3"/>
        <rect x="98" y="6.5" width="12" height="9"/>
        <path d="M98 6.5 l6 5 l6 -5"/>
        <path d="M126 16 c-4 -4 -5 -5.5 -5 -7.5 a5 5 0 0 1 10 0 c0 2 -1 3.5 -5 7.5z"/>
      </g>
    </svg>
    <ul class="contact-list">
      <li>087 5290 418</li>
      <li>info@thrivelane.com</li>
      <li>www.thrivelane.com</li>
    </ul>
  </section>

  <section class="card card--brand">
    <div class="brand">
      <span class="brand-dot" aria-hidden="true"></span>
      <span class="brand-name">Thrive Lane</span>
    </div>
    <p class="tagline">Caring For Your Psychological Well-Being Is Our Top Priority</p>
  </section>
</body>
</html>
```